Graphic Design Project

Brinley-Cote Publications needs a graphic design for a new product called the "KORV Guide". We develop reference field guides for the construction industry and need the "KORV Guide" design to be worthy of its uniqueness.
The design can be in any color combination but must have a watermark or creative design to go with the name. We are getting ready to head start our 2012 volumes and need a new look.
Please do not add anything that looks like construction. We want a powerful look that is creative in nature with a new twist.
Please do not add Brinley-Cote Publications into the design since we already have a logo. Please stay true to "KORV Guide" and knock our socks off.
You always do.
Reason: I did not receive as many designs as I would have expected. I responded to all designers with feedback but was handicapped with the absence of attendees who had accepted my project. I submitted a written concern to Pixel Harbor a few days ago with no response.
Please help me by increasing my deadline to ensure I receive the design I so critically need to move my business forward successfully.
Thank you.
Graphic Design

```html
<!DOCTYPE html>
<html lang="en">
<head>
<meta charset="utf-8">
<title>KORV Guide – Cover</title>
<link rel="stylesheet" href="https://fonts.googleapis.com/css2?family=Alfa+Slab+One&family=Ultra&family=Archivo+Black&family=Roboto+Slab:wght@400&display=block">
<style>
  :root {
    --bg-deep: #2a0000;
    --bg-mid: #5c0606;
    --bg-warm: #8e1010;
    --hex-red: #b50000;
    --hex-light: #e23a3a;
    --hex-dark: #6e0000;
    --watermark: #a51414;
    --title-white: #ffffff;
    --title-shadow: #5a5a5a;
    --subtitle-grey: #cfcfcf;
  }
  html, body {
    margin: 0;
    padding: 0;
    width: 840px;
    height: 1200px;
    overflow: hidden;
    background: var(--bg-deep);
  }
  .cover {
    display: block;
    width: 840px;
    height: 1200px;
  }
  .watermark-top {
    font-family: "Archivo Black", sans-serif;
    fill: var(--watermark);
    opacity: 0.5;
  }
  .watermark-bottom {
    font-family: "Archivo Black", sans-serif;
    fill: var(--watermark);
    opacity: 0.6;
  }
  .title-main,
  .title-main-shadow {
    font-family: "Ultra", "Alfa Slab One", "Rockwell Extra Bold", "Rockwell", serif;
    font-weight: 900;
  }
  .title-main { fill: var(--title-white); }
  .title-main-shadow { fill: var(--title-shadow); }
  .title-sub {
    font-family: "Roboto Slab", serif;
    font-weight: 400;
    fill: var(--subtitle-grey);
  }
</style>
</head>
<body>
<svg class="cover" viewBox="0 0 827 1181" preserveAspectRatio="none" xmlns="http://www.w3.org/2000/svg">
  <defs>
    <linearGradient id="backdrop-tone" x1="0" y1="0" x2="0.4" y2="1">
      <stop offset="0" stop-color="var(--bg-warm)"/>
      <stop offset="0.45" stop-color="var(--bg-mid)"/>
      <stop offset="1" stop-color="var(--bg-deep)"/>
    </linearGradient>
    <linearGradient id="hex-bevel" x1="0" y1="0" x2="1" y2="1">
      <stop offset="0" stop-color="var(--hex-light)"/>
      <stop offset="0.5" stop-color="var(--hex-red)"/>
      <stop offset="1" stop-color="var(--hex-dark)"/>
    </linearGradient>
    <filter id="hex-drop" x="-20%" y="-20%" width="140%" height="140%">
      <feDropShadow dx="6" dy="8" stdDeviation="3" flood-color="#000" flood-opacity="0.9"/>
    </filter>
  </defs>

  <rect class="backdrop-photo" x="0" y="0" width="827" height="1181" fill="url(#backdrop-tone)"
        role="img" aria-label="Red-tinted photograph of a high-rise building under construction with a tower crane and rubble"/>

  <text class="watermark-top" x="335" y="140" font-size="190" textLength="480" lengthAdjust="spacingAndGlyphs">KORV</text>

  <g class="hex-cluster" fill="var(--hex-red)" stroke="url(#hex-bevel)" stroke-width="5" filter="url(#hex-drop)">
    <polygon points="-20,85 32,-6 138,-6 190,85 138,176 32,176"/>
    <polygon points="148,190 207,88 325,88 384,190 325,292 207,292"/>
    <polygon points="-48,302 11,200 129,200 188,302 129,404 11,404"/>
    <polygon points="345,302 404,200 522,200 581,302 522,404 404,404"/>
    <polygon points="540,190 590,104 690,104 740,190 690,276 590,276"/>
    <polygon points="148,415 207,313 325,313 384,415 325,517 207,517"/>
    <polygon points="238,711 395,428 709,428 866,711 709,994 395,994"/>
    <polygon points="74,810 125,723 227,723 278,810 227,897 125,897"/>
    <polygon points="-90,906 -40,820 60,820 110,906 60,992 -40,992"/>
    <polygon points="77,1001 127,915 227,915 277,1001 227,1087 127,1087"/>
  </g>

  <text class="watermark-bottom" x="0" y="1192" font-size="150" textLength="822" lengthAdjust="spacingAndGlyphs">DEMOLITION</text>

  <g class="title-block">
    <text class="title-main-shadow" x="163" y="704" font-size="200" textLength="567" lengthAdjust="spacingAndGlyphs">KORV</text>
    <text class="title-main" x="158" y="700" font-size="200" textLength="567" lengthAdjust="spacingAndGlyphs">KORV</text>
    <text class="title-sub" font-size="30" text-anchor="middle">
      <tspan x="752" y="567">G</tspan>
      <tspan x="752" y="601">U</tspan>
      <tspan x="752" y="635">I</tspan>
      <tspan x="752" y="669">D</tspan>
      <tspan x="752" y="703">E</tspan>
    </text>
  </g>
</svg>
</body>
</html>
```